Puffy Clouds Cotton Candy

Looking for a logo design and business cards to help a 13 year old entrepreneur promote her cotton candy business.
Contact Information for Business Card
Name, Phone & Email
Colors
E54698
E96AAD
F1A4CE
F9D9EA
FCEFF6
A7469A
B969AE
D3A5CF
EDDBEB
F8F0F9
6B429C
8869AF
B7A5CE
E3DAEB
F3F0F8
Requirements
Must have
- A fun feel that is appropriate for a teenage girl selling cotton candy

```html
<!DOCTYPE html>
<html lang="en">
<head>
<meta charset="utf-8">
<title>Puffy Clouds Cotton Candy – Business Cards</title>
<link rel="stylesheet" href="https://fonts.googleapis.com/css2?family=Fredoka:wght@600&family=Quicksand:wght@700&display=swap">
<style>
  :root {
    --pink-strong: #E54698;
    --pink-card: #E96AAD;
    --pink-soft: #F1A4CE;
    --pink-pale: #F9D9EA;
    --violet: #6B429C;
    --white: #FFFFFF;
    --backdrop: #EFEAE6;
  }
  * { margin: 0; padding: 0; box-sizing: border-box; }
  html, body {
    width: 1200px; height: 1200px; overflow: hidden;
    background: var(--backdrop);
  }
  .stage { position: relative; width: 1200px; height: 1200px; }
  .card {
    position: absolute; top: 480px;
    width: 423px; height: 240px;
    border-radius: 18px; overflow: hidden;
  }
  .card--front { left: 152px; background: var(--white); }
  .card--back { left: 624px; background: var(--pink-card); }

  .brand {
    position: absolute; left: 24px; top: 30px;
    display: flex; align-items: center; gap: 10px;
  }
  .brand__dot {
    width: 46px; height: 46px; border-radius: 50%;
    background: var(--pink-soft);
  }
  .brand__name {
    font-family: "Fredoka", sans-serif; font-weight: 600;
    color: var(--pink-strong); font-size: 21px; line-height: 1.05;
  }

  .holder {
    position: absolute; left: 40px; top: 154px;
    font-family: "Fredoka", sans-serif; font-weight: 600;
    font-size: 20px; color: var(--pink-strong);
  }
  .divider {
    position: absolute; left: 40px; right: 0; top: 184px;
    height: 1.5px; background: var(--violet);
  }
  .contact {
    position: absolute; left: 40px; top: 194px;
    list-style: none;
    font-family: "Quicksand", sans-serif; font-weight: 700;
    font-size: 11.5px; color: var(--violet);
  }
  .contact__item { display: flex; align-items: center; gap: 9px; height: 15px; }
  .contact__icon { width: 12px; height: 12px; flex: none; }

  .emblem {
    position: absolute; left: 50%; top: 50%;
    width: 200px; height: 200px; margin: -100px 0 0 -100px;
    border-radius: 50%; background: var(--pink-pale);
    display: flex; align-items: center; justify-content: center;
  }
  .emblem__name {
    font-family: "Fredoka", sans-serif; font-weight: 600;
    color: var(--pink-strong); font-size: 38px; line-height: 1.05;
    text-align: center;
  }
</style>
</head>
<body>
<main class="stage">
  <section class="card card--front" aria-label="Business card front">
    <div class="brand">
      <span class="brand__dot"></span>
      <p class="brand__name">Puffy Clouds<br>Cotton Candy</p>
    </div>
    <h1 class="holder">Mia Harlow</h1>
    <div class="divider"></div>
    <ul class="contact">
      <li class="contact__item">
        <svg class="contact__icon" viewBox="0 0 24 24" aria-hidden="true">
          <path fill="#E54698" d="M6.6 10.8a15.1 15.1 0 0 0 6.6 6.6l2.2-2.2a1 1 0 0 1 1-.25 11.4 11.4 0 0 0 3.6.57 1 1 0 0 1 1 1V20a1 1 0 0 1-1 1A17 17 0 0 1 3 4a1 1 0 0 1 1-1h3.5a1 1 0 0 1 1 1c0 1.25.2 2.45.57 3.57a1 1 0 0 1-.25 1z"/>
        </svg>
        <span>07. 4821. 3396</span>
      </li>
      <li class="contact__item">
        <svg class="contact__icon" viewBox="0 0 24 24" aria-hidden="true">
          <rect x="2" y="5" width="20" height="14" fill="#E54698"/>
          <path d="M2 5l10 8 10-8" fill="none" stroke="#fff" stroke-width="1.8"/>
        </svg>
        <span>mia@puffyclouds.com</span>
      </li>
    </ul>
  </section>

  <section class="card card--back" aria-label="Business card back">
    <div class="emblem">
      <p class="emblem__name">Puffy Clouds<br>Cotton Candy</p>
    </div>
  </section>
</main>
</body>
</html>
```